Business Card Design

We need a design for business cards for our company. We have a logo. We teach EMT's and we are based out of Virginia. The information that will need to add would be, name, title, phone number, email, address. On the back of the business card would be "We help you, help others"

Target Market(s)

People that want to become EMT's

Colors

Designer to choose colors to be used in the design.

Requirements
Must have
• company logo

```html
<!DOCTYPE html>
<html lang="en">
<head>
<meta charset="utf-8">
<title>Crest Response Training — Business Card</title>
<link href="https://fonts.googleapis.com/css2?family=Montserrat:wght@400;600&family=Lato:wght@400;700&display=swap" rel="stylesheet">
<style>
  :root {
    --page: #e6e7ea;
    --card: #1c2232;
    --card-deep: #151a27;
    --card-light: #232a3d;
    --pattern: #2a3347;
    --red: #e8223f;
    --steel: #a9bccd;
    --white: #f2f4f7;
    --muted: #8793a6;
  }
  * { box-sizing: border-box; margin: 0; padding: 0; }
  html, body { width: 1200px; height: 900px; overflow: hidden; }
  body {
    background: var(--page);
    display: flex;
    flex-direction: column;
    align-items: center;
    justify-content: center;
    gap: 22px;
  }
  .card {
    position: relative;
    width: 735px;
    height: 420px;
    background: linear-gradient(135deg, var(--card-light) 0%, var(--card) 50%, var(--card-deep) 100%);
    border-radius: 4px;
    overflow: hidden;
    box-shadow: 0 10px 28px rgba(0,0,0,.25);
  }
  .cross-pattern {
    position: absolute;
    right: 0;
    top: 0;
    width: 300px;
    height: 100%;
    background: linear-gradient(100deg, rgba(42,51,71,0) 0%, rgba(42,51,71,.55) 60%, rgba(42,51,71,.8) 100%);
  }
  .wordmark {
    position: absolute;
    display: flex;
    align-items: center;
    gap: 14px;
    font-family: "Montserrat", sans-serif;
    font-weight: 600;
    color: var(--red);
    letter-spacing: .02em;
    white-space: nowrap;
  }
  .wordmark .dot {
    width: 22px;
    height: 22px;
    border-radius: 50%;
    background: var(--red);
    flex: none;
  }
  .card--front .wordmark { left: 130px; top: 150px; font-size: 36px; }
  .tagline {
    position: absolute;
    left: 330px;
    top: 260px;
    font-family: "Montserrat", sans-serif;
    font-size: 15px;
    letter-spacing: .06em;
    color: var(--white);
  }
  .card--back .wordmark { left: 150px; top: 100px; font-size: 30px; }
  .identity {
    position: absolute;
    right: 400px;
    top: 290px;
    text-align: right;
    font-family: "Lato", sans-serif;
  }
  .identity .person-name {
    font-size: 22px;
    color: var(--red);
    letter-spacing: .02em;
  }
  .identity .person-name strong { font-weight: 700; }
  .identity .person-name span { font-weight: 400; }
  .identity .person-title {
    font-size: 15px;
    color: var(--white);
    margin-top: 4px;
  }
  .divider {
    position: absolute;
    left: 350px;
    top: 270px;
    width: 1px;
    height: 90px;
    background: var(--muted);
  }
  .contact {
    position: absolute;
    left: 372px;
    top: 276px;
    list-style: none;
    font-family: "Lato", sans-serif;
    font-size: 15px;
    color: var(--white);
  }
  .contact li { display: flex; align-items: center; gap: 10px; height: 26px; }
  .contact svg { width: 14px; height: 14px; flex: none; }
  .contact .web { color: var(--red); font-weight: 700; padding-left: 24px; }
</style>
</head>
<body>

  <section class="card card--front" aria-label="Card front">
    <div class="cross-pattern" role="img" aria-label="Faint pattern of medical crosses"></div>
    <div class="wordmark"><span class="dot"></span>CREST RESPONSE TRAINING</div>
    <p class="tagline">WE HELP YOU, HELP OTHERS</p>
  </section>

  <section class="card card--back" aria-label="Card back">
    <div class="cross-pattern" role="img" aria-label="Faint pattern of medical crosses"></div>
    <div class="wordmark"><span class="dot"></span>CREST RESPONSE TRAINING</div>

    <div class="identity">
      <p class="person-name"><strong>DANA</strong> <span>HALVORSEN</span></p>
      <p class="person-title">Founder / Director</p>
    </div>

    <div class="divider"></div>

    <ul class="contact">
      <li>
        <svg viewBox="0 0 24 24" fill="var(--red)" aria-hidden="true"><path d="M6.6 10.8a15 15 0 0 0 6.6 6.6l2.2-2.2a1 1 0 0 1 1-.25 11.4 11.4 0 0 0 3.6.57 1 1 0 0 1 1 1V20a1 1 0 0 1-1 1A17 17 0 0 1 3 4a1 1 0 0 1 1-1h3.5a1 1 0 0 1 1 1c0 1.25.2 2.45.57 3.57a1 1 0 0 1-.25 1z"/></svg>
        +1 540 555 0142
      </li>
      <li>
        <svg viewBox="0 0 24 24" fill="var(--red)" aria-hidden="true"><path d="M3 5h18v14H3z M3 5l9 7 9-7" stroke="var(--card)" stroke-width="1.6"/></svg>
        info@crestresponse.com
      </li>
      <li class="web">www.crestresponse.com</li>
    </ul>
  </section>

</body>
</html>
```